Family business needs stationery redesign with new logo

Family owned company, established in 1987 wanting a brand 'refresh'. We are an electrical, refrigeration and construction company based in the Barkly Region Northern Territory, Australia. We have a new logo we would like to use which is uploaded along with our current letterhead and email signature. We are also dropping the word 'contractors' so please do not include this on any designs. Please note also, the 'orange' color used in our logo and designs should be Northern Territory red ochre which is as follows:

RGB (Hex): #C75B12
PantoneĀ® 159 C
CMYK: 1 / 74 / 100 / 7

We are needing our stationery redesigned using our new logo. Please include letterheads, business cards, envelopes, and email signatures.

We currently use our business letterheads for quotations, invoices, letters, HR matters, and internal memos.

We also need a separate simplified letterhead for internal paperwork such as employee leave forms, meeting agendas, and meeting minutes etc.

Reason: Needing more submissions of full package designs. We are wanting all our stationery, including business cards, letterheads, email signatures, envelopes, etc to be cohesive. We also require ALL the information, as supplied on our template letterhead, to be included on the new letterhead designs. including electrical license no.etc Thank you, R&W

Reason: needing more time as work has got in the way of looking over designs. A lot of designs not meeting the brief/criteria.

Industry/Entity Type

Business

Colors
0355a3
f37122

Requirements
Must have
• The 'orange' color used in the designs should be Northern Territory red ochre which is as follows:
• RGB (Hex): #C75B12
• PantoneĀ® 159 C
• CMYK: 1 / 74 / 100 / 7
• ***MUST INCLUDE ALL INFORMATION THAT IS ON OUR CURRENT LETTERHEAD***
Should not have
• Please do not include the word 'contractors'

```html
<!DOCTYPE html>
<html lang="en">
<head>
<meta charset="utf-8">
<title>R&amp;W Business Card</title>
<link rel="stylesheet" href="https://fonts.googleapis.com/css2?family=Arimo:wght@400;700&display=swap">
<style>
  :root {
    --page-bg: #e7e4df;
    --card-bg: #f5f5f3;
    --card-edge: #d8d8d6;
    --navy: #222d5e;
    --ochre: #c75b12;
    --white: #ffffff;
  }
  * { margin: 0; padding: 0; box-sizing: border-box; }
  html, body {
    width: 1200px;
    height: 969px;
    overflow: hidden;
    background: var(--page-bg);
    font-family: "Arimo", Arial, sans-serif;
  }
  .business-card {
    position: absolute;
    left: 100px;
    top: 201px;
    width: 1000px;
    height: 567px;
    background: var(--card-bg);
    border: 1px solid var(--card-edge);
    border-radius: 30px;
    overflow: hidden;
    box-shadow: 0 12px 30px rgba(0,0,0,0.12);
  }
  .card-shapes {
    position: absolute;
    inset: 0;
  }
  .brand-name {
    position: absolute;
    left: 560px;
    top: 70px;
    width: 364px;
    text-align: center;
    font-weight: 700;
    font-size: 104px;
    line-height: 1;
    color: var(--navy);
    letter-spacing: 2px;
  }
  .contact-block {
    position: absolute;
    left: 46px;
    top: 305px;
    color: var(--white);
    font-size: 25px;
    line-height: 1.38;
  }
  .contact-address { margin-bottom: 22px; }
  .contact-line {
    display: flex;
    align-items: center;
    gap: 12px;
    line-height: 1.45;
  }
  .contact-line svg { width: 22px; height: 22px; flex: none; }
  .person {
    position: absolute;
    right: 62px;
    top: 460px;
    text-align: right;
  }
  .person-name {
    font-weight: 700;
    font-size: 34px;
    color: var(--navy);
    letter-spacing: 0.5px;
  }
  .person-title {
    font-size: 26px;
    color: var(--ochre);
    margin-top: 6px;
  }
</style>
</head>
<body>
  <div class="business-card">
    <svg class="card-shapes" viewBox="0 0 1000 567" width="1000" height="567" aria-hidden="true">
      <path d="M0,155 C300,168 505,330 528,567 L0,567 Z" fill="var(--navy)"/>
      <path d="M0,170 C290,183 488,338 510,567" fill="none" stroke="var(--ochre)" stroke-width="4"/>
    </svg>

    <div class="brand-name">R&amp;W</div>

    <div class="contact-block">
      <p class="contact-address">42 Ironbark Road<br>Tennant Creek, NT 0860</p>
      <p class="contact-line">
        <svg viewBox="0 0 24 24"><path fill="var(--ochre)" d="M6.6 10.8a15.1 15.1 0 0 0 6.6 6.6l2.2-2.2c.3-.3.7-.4 1-.2 1.1.4 2.3.6 3.6.6.6 0 1 .4 1 1V20c0 .6-.4 1-1 1A17 17 0 0 1 3 4c0-.6.4-1 1-1h3.5c.6 0 1 .4 1 1 0 1.3.2 2.5.6 3.6.1.3 0 .7-.2 1z"/></svg>
        08 8962 1140
      </p>
      <p class="contact-line">
        <svg viewBox="0 0 24 24"><path fill="var(--ochre)" d="M6 2h12v6H6zM3 9h18v9h-3v4H6v-4H3zm5 7v4h8v-4z"/></svg>
        08 8962 1141
      </p>
      <p class="contact-line">
        <svg viewBox="0 0 24 24"><path fill="var(--ochre)" d="M2 5h20v14H2zm2 2v.5l8 5 8-5V7z"/></svg>
        office@rwbarkly.com
      </p>
      <p class="contact-line">
        <svg viewBox="0 0 24 24"><circle cx="12" cy="12" r="10" fill="var(--ochre)"/><path d="M2 12h20M12 2c3 3 3 17 0 20M12 2c-3 3-3 17 0 20" stroke="var(--navy)" stroke-width="1.4" fill="none"/></svg>
        www.rwbarkly.com
      </p>
    </div>

    <div class="person">
      <p class="person-name">DANIEL REEVE</p>
      <p class="person-title">CEO/Founder</p>
    </div>
  </div>
</body>
</html>
```